Animal Horse & Bedding Company Needs a Website Coded & Designed

We need a website for a new animal bedding and feed company that is visually grabbing and vibrant. We would like to see a website that displays trust, quality and confidence. Needs to be responsive and mobile friendly for all browsers and coded for both Android & IOS. SEO is also important.

Joomla or Wordpress – must be both desktop and mobile friendly with fast page load speed. Need the ability to edit ourselves in Wordpress or Joomla.

Full details attached below with some layout and content ideas.

Coding

Coded - Design and coding required

Number of Pages Required

5+ page

Font styles to use
Sans Serif

Requirements
Must have
• Needs to be responsive and mobile friendly for all browsers and coded for both Android & IOS. SEO is also important.

Wordpress – must be both desktop and mobile friendly with fast page load speed. Need the ability to edit ourselves in Wordpress.

Logo Colours:
Dark Brown
CMYK: 50 / 70 / 80 / 70
Pantone: 4625C

Orange
CMYK: 0 / 50 / 100 / 0
Pantone: 144C
Nice to have
• Use picture of building attached and super impose logo on building.

```html
<!DOCTYPE html>
<html lang="en">
<head>
<meta charset="utf-8">
<title>Golden Sheaf Bedding &amp; Feed</title>
<link href="https://fonts.googleapis.com/css2?family=Titillium+Web:wght@400;600;700&family=Open+Sans:wght@400;600&display=swap" rel="stylesheet">
<style>
:root{
  --brown:#3a2a22;
  --brown-deep:#2a1d17;
  --orange:#f5821f;
  --orange-dark:#e47212;
  --white:#ffffff;
  --ink:#2b2b2b;
  --grey-bg:#f3f3f3;
  --footer:#201a17;
  --footer-text:#d9d4d0;
}
*{box-sizing:border-box;margin:0;padding:0}
html,body{width:1200px;height:4181px;overflow:hidden}
body{position:relative;background:var(--white);font-family:"Open Sans",sans-serif;color:var(--ink)}
.abs{position:absolute}
.heading{font-family:"Titillium Web",sans-serif;font-weight:700;text-transform:uppercase}
.btn{position:absolute;display:flex;align-items:center;justify-content:center;font-family:"Titillium Web",sans-serif;font-weight:700;font-size:15px;text-transform:uppercase;letter-spacing:.3px;border-radius:4px}
.btn-orange{background:var(--orange);color:var(--white)}
.btn-outline-dark{border:2px solid var(--brown);color:var(--brown);background:var(--white)}
.btn-outline-light{border:2px solid var(--white);color:var(--white)}
.btn-pill{border-radius:30px}

/* header + hero */
.hero-photo{left:0;top:0;width:1200px;height:850px;background:linear-gradient(180deg,#3b2b1f 0%,#6b5a2e 14%,#8a8d3e 40%,#5e7a2c 70%,#3f5a1f 100%)}
.hero-photo::after{content:"";position:absolute;left:0;top:0;width:640px;height:850px;background:radial-gradient(ellipse at 40% 45%,rgba(120,50,20,.85) 0%,rgba(110,50,25,.5) 45%,rgba(0,0,0,0) 75%)}
.hero-curve{left:0;top:740px}
.brand{display:flex;flex-direction:column;align-items:center;gap:10px}
.brand-mark{width:44px;height:44px;border-radius:50%;background:var(--orange)}
.brand-name{font-family:"Titillium Web",sans-serif;font-weight:600;color:var(--white);font-size:34px;letter-spacing:3px;line-height:1;white-space:nowrap}
.header-brand{left:146px;top:36px;width:244px}
.call{left:645px;top:38px;display:flex;align-items:center;gap:12px;color:var(--white)}
.call-icon{width:40px;height:40px;border-radius:50%;background:var(--orange);display:flex;align-items:center;justify-content:center}
.call small{display:block;font-size:13px;font-weight:600}
.call strong{display:block;font-family:"Titillium Web",sans-serif;font-size:19px;line-height:1.1}
.nav{left:471px;top:109px;width:585px;height:49px}
.nav-list{position:absolute;left:62px;top:0;height:49px;display:flex;align-items:center;list-style:none;font-family:"Titillium Web",sans-serif;font-weight:700;font-size:15px;color:var(--white)}
.nav-list li{margin-right:40px;position:relative}
.nav-list li.active::after{content:"";position:absolute;left:0;right:0;bottom:-13px;height:3px;background:var(--orange)}
.hero-title{right:144px;top:365px;text-align:right;color:var(--white);font-size:50px;line-height:58px;text-shadow:0 2px 6px rgba(0,0,0,.35)}
.slider-dots{left:985px;top:578px;display:flex;gap:8px}
.slider-dots span{width:16px;height:16px;border:2px solid var(--white);border-radius:50%}
.slider-dots span:first-child{width:22px;height:22px;margin-top:-3px}

/* feature circles */
.feature{border-radius:50%;display:flex;flex-direction:column;align-items:center;text-align:center;color:var(--white)}
.feature-dark{background:var(--brown);width:290px;height:290px;border:5px solid var(--white)}
.feature-main{background:var(--orange);width:352px;height:352px;border:6px solid var(--white)}
.feature h3{font-family:"Titillium Web",sans-serif;font-weight:700;text-transform:uppercase;line-height:1.2}
.feature p{font-size:16.5px;line-height:22px}

/* welcome */
.welcome-image{left:143px;top:1096px;width:360px;height:482px}
.welcome-title{left:573px;top:1165px;font-size:37px;line-height:43px;color:var(--brown-deep)}
.welcome-text{left:573px;top:1274px;width:482px;font-size:15px;line-height:25px;color:#444}

/* bedding & feed bands */
.band-bg{background:var(--grey-bg)}
.offer{background:var(--orange);color:var(--white)}
.offer h2{font-family:"Titillium Web",sans-serif;font-weight:700;font-size:34px;line-height:1;text-transform:uppercase}
.offer .lead{font-size:15px;line-height:25px}
.offer h4{font-family:"Titillium Web",sans-serif;font-weight:700;font-size:15px;text-transform:uppercase;letter-spacing:.3px}
.benefits{list-style:none}
.benefits li{display:flex;align-items:center;gap:12px;font-size:15px;height:30.5px}
.tick{width:15px;height:15px;flex:none}

/* newsletter */
.newsletter-mark{left:568px;top:3252px;width:64px;height:64px;border-radius:50%;background:var(--orange)}
.newsletter-title{left:0;width:1200px;top:3360px;text-align:center;font-family:"Titillium Web",sans-serif;font-weight:700;font-size:46px;color:var(--brown-deep)}
.newsletter-sub{left:0;width:1200px;top:3416px;text-align:center;font-size:16px;color:#333}
.field{background:var(--white);box-shadow:0 2px 6px rgba(0,0,0,.12);height:57px;display:flex;align-items:center;padding-left:24px;font-size:14px;color:#777}
.landscape{left:0;top:3545px;width:1200px;height:150px;background:linear-gradient(180deg,rgba(243,243,243,0) 0%,#9aa08a 30%,#5f6b4a 65%,#3c4530 100%)}

/* footer */
.footer{left:0;top:3695px;width:1200px;height:486px;background:var(--footer);color:var(--footer-text)}
.footer-brand{left:143px;top:84px;width:295px}
.footer-brand .brand-name{font-size:38px}
.delivery{left:146px;top:251px;width:288px;height:46px;background:var(--orange);border-radius:24px;display:flex;align-items:center;gap:12px;padding-left:8px;font-family:"Titillium Web",sans-serif;font-weight:700;font-size:16px;color:var(--white);text-transform:uppercase}
.delivery-icon{width:34px;height:34px;border-radius:50%;background:var(--brown-deep);display:flex;align-items:center;justify-content:center}
.footer-heading{font-family:"Titillium Web",sans-serif;font-weight:700;font-size:19px;color:var(--white);text-transform:uppercase}
.contact-row{display:flex;gap:18px;align-items:center}
.contact-icon{width:44px;height:44px;border:2px solid var(--white);border-radius:50%;display:flex;align-items:center;justify-content:center;flex:none}
.contact-row b{display:block;color:var(--white);font-size:15px;font-weight:600}
.contact-row span{font-size:15px}
.sitemap{list-style:none;font-size:14px;line-height:29.6px}
.footer-rule{left:0;top:373px;width:1200px;height:1px;background:#3a312c}
.copyright{left:143px;top:422px;font-size:15px}
.social{width:36px;height:36px;border:2px solid var(--orange);border-radius:50%}
</style>
</head>
<body>

<!-- hero -->
<div class="abs hero-photo" role="img" aria-label="Chestnut horse with a white blaze galloping through a sunlit green field"></div>
<svg class="abs hero-curve" width="1200" height="110" viewBox="0 0 1200 110" aria-hidden="true">
  <path d="M0 36 Q600 150 1200 72 L1200 110 L0 110 Z" fill="#ffffff"/>
</svg>

<header>
  <div class="abs brand header-brand">
    <span class="brand-mark"></span>
    <span class="brand-name">GOLDEN SHEAF</span>
  </div>
  <div class="abs call">
    <span class="call-icon">
      <svg width="20" height="20" viewBox="0 0 24 24"><path d="M6.6 10.8a15 15 0 0 0 6.6 6.6l2.2-2.2a1 1 0 0 1 1-.25 11 11 0 0 0 3.6.6 1 1 0 0 1 1 1V20a1 1 0 0 1-1 1A17 17 0 0 1 3 4a1 1 0 0 1 1-1h3.5a1 1 0 0 1 1 1 11 11 0 0 0 .6 3.6 1 1 0 0 1-.25 1z" fill="#fff"/></svg>
    </span>
    <div><small>Call Us</small><strong>555 0142 7788</strong></div>
  </div>
  <div class="btn btn-orange btn-pill" style="left:866px;top:36px;width:190px;height:44px">Request Quote</div>
  <nav class="abs nav">
    <svg class="abs" style="left:0;top:0" width="585" height="49" viewBox="0 0 585 49" aria-hidden="true">
      <polygon points="36,0 585,0 567,49 44,49" fill="#2a1d17"/>
      <polygon points="0,0 30,0 15,30" fill="#f5821f"/>
      <polygon points="585,30 585,49 573,49" fill="#f5821f"/>
    </svg>
    <ul class="nav-list">
      <li class="active">HOME</li><li>ABOUT</li><li>FEED</li><li>BEDDING</li><li>CONTACT US</li>
    </ul>
  </nav>
</header>

<h1 class="abs heading hero-title">Golden Sheaf<br>Bedding &amp; Feed</h1>
<div class="btn btn-orange btn-pill" style="left:882px;top:499px;width:174px;height:44px">Learn More</div>
<div class="abs slider-dots"><span></span><span></span><span></span></div>

<!-- features -->
<section>
  <div class="abs feature feature-dark" style="left:139px;top:764px">
    <svg style="margin-top:30px" width="76" height="76" viewBox="0 0 76 76" aria-hidden="true">
      <circle cx="38" cy="34" r="24" fill="none" stroke="#fff" stroke-width="3"/>
      <circle cx="38" cy="34" r="16" fill="none" stroke="#fff" stroke-width="2"/>
      <polyline points="30,34 36,40 47,28" fill="none" stroke="#fff" stroke-width="3"/>
      <polyline points="26,54 20,70 28,66 32,72 36,58" fill="none" stroke="#fff" stroke-width="2"/>
      <polyline points="50,54 56,70 48,66 44,72 40,58" fill="none" stroke="#fff" stroke-width="2"/>
    </svg>
    <h3 style="font-size:19px;margin-top:10px">Quality<br>Guaranteed</h3>
    <p style="margin-top:12px;width:210px">Grown for quality 100% natural with no chemicals or additives</p>
  </div>

  <div class="abs feature feature-main" style="left:423px;top:717px">
    <svg style="margin-top:40px" width="80" height="80" viewBox="0 0 80 80" aria-hidden="true">
      <rect x="14" y="6" width="44" height="60" fill="none" stroke="#fff" stroke-width="3"/>
      <line x1="22" y1="20" x2="50" y2="20" stroke="#fff" stroke-width="3"/>
      <line x1="22" y1="30" x2="50" y2="30" stroke="#fff" stroke-width="3"/>
      <line x1="22" y1="40" x2="42" y2="40" stroke="#fff" stroke-width="3"/>
      <line x1="22" y1="50" x2="38" y2="50" stroke="#fff" stroke-width="3"/>
      <line x1="44" y1="62" x2="68" y2="30" stroke="#fff" stroke-width="5"/>
    </svg>
    <h3 style="font-size:24px;margin-top:12px">Full Service<br>Solution</h3>
    <p style="margin-top:10px;width:230px;font-size:18px;line-height:23px">Dedicated in providing a full service solution of bedding supply &amp; waste removal</p>
  </div>

  <div class="abs feature feature-dark" style="left:769px;top:764px">
    <svg style="margin-top:30px" width="80" height="76" viewBox="0 0 80 76" aria-hidden="true">
      <rect x="8" y="30" width="40" height="30" fill="none" stroke="#fff" stroke-width="3"/>
      <rect x="14" y="36" width="16" height="10" fill="none" stroke="#fff" stroke-width="2"/>
      <line x1="4" y1="66" x2="60" y2="66" stroke="#fff" stroke-width="3"/>
      <circle cx="56" cy="22" r="12" fill="none" stroke="#fff" stroke-width="3"/>
      <circle cx="56" cy="22" r="4" fill="#fff"/>
      <rect x="50" y="44" width="16" height="16" fill="none" stroke="#fff" stroke-width="2"/>
    </svg>
    <h3 style="font-size:18px;margin-top:8px">Convenient and<br>Cost Effective</h3>
    <p style="margin-top:10px;width:210px">Compressed bags , pellets or bulk products saving in shipping costs</p>
  </div>
</section>

<!-- welcome -->
<section>
  <svg class="abs welcome-image" viewBox="0 0 360 482" role="img" aria-label="Aerial photo of the farm and stables framed in a round shape">
    <defs>
      <linearGradient id="farmTone" x1="0" y1="0" x2="0" y2="1">
        <stop offset="0" stop-color="#b9c4cf"/><stop offset=".45" stop-color="#6d7a5c"/><stop offset="1" stop-color="#4a3f35"/>
      </linearGradient>
    </defs>
    <circle cx="180" cy="300" r="172" fill="url(#farmTone)" stroke="#2a1d17" stroke-width="8"/>
  </svg>
  <h2 class="abs heading welcome-title">Welcome to Golden Sheaf<br>Bedding and Feed</h2>
  <p class="abs welcome-text">Sed ut perspiciatis unde omnis iste natus error sit voluptatem accusantium doloremque laudantium, totam rem aperiam, eaque ipsa quae ab illo inventore veritatis et quasi architecto beatae vitae dicta sunt explicabo. Nemo enim ipsam voluptatem quia voluptas sit aspernatur aut odit aut fugit, sed quia consequuntur magni dolores eos qui ratione voluptatem sequi nesciunt. Neque porro quisquam est, qui dolorem ipsum quia dolor sit amet, consectetur</p>
  <div class="btn btn-outline-dark" style="left:573px;top:1481px;width:150px;height:43px">Learn More</div>
  <div class="btn btn-orange" style="left:740px;top:1481px;width:174px;height:43px">Request Quote</div>
</section>

<!-- bedding -->
<section>
  <div class="abs band-bg" style="left:0;top:1656px;width:1200px;height:715px"></div>
  <div class="abs" style="left:351px;top:1656px;width:849px;height:715px;background:linear-gradient(180deg,#8fa3b8 0%,#c9c0a2 35%,#6b8a3a 60%,#3d5a1f 100%)" role="img" aria-label="Brown cattle grazing in a sunny green pasture"></div>
  <div class="abs offer" style="left:0;top:1726px;width:685px;height:577px">
    <h2 class="abs" style="left:141px;top:42px">Bedding</h2>
    <p class="abs lead" style="left:141px;top:92px;width:400px">Sed ut perspiciatis unde omnis iste natus voluptatem accusantium doloremque laudantium, totam rem apem, eaque ipsa quae ab illo inventore veritatis et quasi arcto beatae vitae dicta sunt explicabo</p>
    <h4 class="abs" style="left:141px;top:212px">Benefits</h4>
    <ul class="abs benefits" style="left:141px;top:248px">
      <li><svg class="tick" viewBox="0 0 16 16"><circle cx="8" cy="8" r="8" fill="#fff"/><polyline points="6,4 10,8 6,12" fill="none" stroke="#f5821f" stroke-width="2"/></svg>100% Natural Chopped Straw</li>
      <li><svg class="tick" viewBox="0 0 16 16"><circle cx="8" cy="8" r="8" fill="#fff"/><polyline points="6,4 10,8 6,12" fill="none" stroke="#f5821f" stroke-width="2"/></svg>Low Dust</li>
      <li><svg class="tick" viewBox="0 0 16 16"><circle cx="8" cy="8" r="8" fill="#fff"/><polyline points="6,4 10,8 6,12" fill="none" stroke="#f5821f" stroke-width="2"/></svg>Chemical &amp; Additive Free</li>
      <li><svg class="tick" viewBox="0 0 16 16"><circle cx="8" cy="8" r="8" fill="#fff"/><polyline points="6,4 10,8 6,12" fill="none" stroke="#f5821f" stroke-width="2"/></svg>Clean &amp; Highly Absorbent</li>
      <li><svg class="tick" viewBox="0 0 16 16"><circle cx="8" cy="8" r="8" fill="#fff"/><polyline points="6,4 10,8 6,12" fill="none" stroke="#f5821f" stroke-width="2"/></svg>Cheaper than Wood Shavings</li>
      <li><svg class="tick" viewBox="0 0 16 16"><circle cx="8" cy="8" r="8" fill="#fff"/><polyline points="6,4 10,8 6,12" fill="none" stroke="#f5821f" stroke-width="2"/></svg>Economic – less used and less wasted</li>
      <li><svg class="tick" viewBox="0 0 16 16"><circle cx="8" cy="8" r="8" fill="#fff"/><polyline points="6,4 10,8 6,12" fill="none" stroke="#f5821f" stroke-width="2"/></svg>Environmentally Friendly – Recyclable &amp; Compostable</li>
    </ul>
    <div class="btn btn-outline-light" style="left:141px;top:491px;width:213px;height:45px">Learn More Bedding</div>
  </div>
</section>

<!-- feed -->
<section>
  <div class="abs band-bg" style="left:0;top:2371px;width:1200px;height:796px"></div>
  <div class="abs" style="left:0;top:2371px;width:987px;height:796px;background:linear-gradient(180deg,#e07a22 0%,#c9853a 30%,#6f7a2e 62%,#3b5320 100%)" role="img" aria-label="Flock of sheep in a meadow at sunset"></div>
  <div class="abs offer" style="left:516px;top:2441px;width:684px;height:656px">
    <h2 class="abs" style="left:72px;top:32px">Feed</h2>
    <p class="abs lead" style="left:72px;top:82px;width:400px">Hay cubes and pellets are made from premium hay offering a variety of animals a feed that is non-GMO and packed with natural nutrients.  These pellets and cubes are less bulky to handle, store and ship. As well, they reduce the amount of wasted feed.</p>
    <h4 class="abs" style="left:72px;top:220px">Benefits</h4>
    <ul class="abs benefits" style="left:72px;top:256px">
      <li><svg class="tick" viewBox="0 0 16 16"><circle cx="8" cy="8" r="8" fill="#fff"/><polyline points="6,4 10,8 6,12" fill="none" stroke="#f5821f" stroke-width="2"/></svg>100% Natural</li>
      <li><svg class="tick" viewBox="0 0 16 16"><circle cx="8" cy="8" r="8" fill="#fff"/><polyline points="6,4 10,8 6,12" fill="none" stroke="#f5821f" stroke-width="2"/></svg>Chemical &amp; Additive Free</li>
      <li><svg class="tick" viewBox="0 0 16 16"><circle cx="8" cy="8" r="8" fill="#fff"/><polyline points="6,4 10,8 6,12" fill="none" stroke="#f5821f" stroke-width="2"/></svg>Available in Pellets or Cubes</li>
      <li><svg class="tick" viewBox="0 0 16 16"><circle cx="8" cy="8" r="8" fill="#fff"/><polyline points="6,4 10,8 6,12" fill="none" stroke="#f5821f" stroke-width="2"/></svg>High Protein Content</li>
      <li><svg class="tick" viewBox="0 0 16 16"><circle cx="8" cy="8" r="8" fill="#fff"/><polyline points="6,4 10,8 6,12" fill="none" stroke="#f5821f" stroke-width="2"/></svg>Eliminate Waste In Feeding</li>
      <li><svg class="tick" viewBox="0 0 16 16"><circle cx="8" cy="8" r="8" fill="#fff"/><polyline points="6,4 10,8 6,12" fill="none" stroke="#f5821f" stroke-width="2"/></svg>Clean - Eliminates Dust From Feeding Baled Hay</li>
      <li><svg class="tick" viewBox="0 0 16 16"><circle cx="8" cy="8" r="8" fill="#fff"/><polyline points="6,4 10,8 6,12" fill="none" stroke="#f5821f" stroke-width="2"/></svg>Cost Effective</li>
      <li><svg class="tick" viewBox="0 0 16 16"><circle cx="8" cy="8" r="8" fill="#fff"/><polyline points="6,4 10,8 6,12" fill="none" stroke="#f5821f" stroke-width="2"/></svg>Convenient</li>
      <li><svg class="tick" viewBox="0 0 16 16"><circle cx="8" cy="8" r="8" fill="#fff"/><polyline points="6,4 10,8 6,12" fill="none" stroke="#f5821f" stroke-width="2"/></svg>Less wasted feed</li>
    </ul>
    <div class="btn btn-outline-light" style="left:72px;top:555px;width:214px;height:45px">Learn More Feed</div>
  </div>
</section>

<!-- newsletter -->
<section>
  <div class="abs band-bg" style="left:0;top:3167px;width:1200px;height:528px"></div>
  <div class="abs landscape" role="img" aria-label="Wide view of farmland and stables under an overcast sky"></div>
  <div class="abs newsletter-mark"></div>
  <h2 class="abs newsletter-title">Join our Newsletter</h2>
  <p class="abs newsletter-sub">Nemo enim ipsam voluptatem quia voluptas sit aspernatur aut odit aut</p>
  <div class="abs field" style="left:216px;top:3467px;width:279px">Name</div>
  <div class="abs field" style="left:513px;top:3467px;width:294px">Email Address*</div>
  <div class="btn btn-orange" style="left:823px;top:3467px;width:161px;height:57px;border-radius:0;font-size:17px">Sign Up</div>
</section>

<!-- footer -->
<footer class="abs footer">
  <div class="abs brand footer-brand">
    <span class="brand-mark"></span>
    <span class="brand-name">GOLDEN SHEAF</span>
  </div>
  <div class="abs delivery">
    <span class="delivery-icon">
      <svg width="20" height="14" viewBox="0 0 20 14"><rect x="0" y="1" width="12" height="9" fill="#f5821f"/><polygon points="12,4 17,4 20,8 20,10 12,10" fill="#f5821f"/><circle cx="4" cy="12" r="2" fill="#f5821f"/><circle cx="15" cy="12" r="2" fill="#f5821f"/></svg>
    </span>
    Delivery in Canada &amp; USA
  </div>
  <div class="abs" style="left:490px;top:62px;width:1px;height:200px;background:#4a3f38"></div>
  <div class="abs" style="left:909px;top:62px;width:1px;height:200px;background:#4a3f38"></div>

  <h3 class="abs footer-heading" style="left:542px;top:68px">Contact Us</h3>
  <div class="abs contact-row" style="left:542px;top:127px">
    <span class="contact-icon"><svg width="16" height="20" viewBox="0 0 16 20"><path d="M8 0a8 8 0 0 0-8 8c0 6 8 12 8 12s8-6 8-12a8 8 0 0 0-8-8z" fill="#f5821f"/><circle cx="8" cy="8" r="3" fill="#201a17"/></svg></span>
    <div><b>Golden Sheaf bedding and feed</b><span>1870 Prairie Line Road</span></div>
  </div>
  <div class="abs contact-row" style="left:542px;top:190px">
    <span class="contact-icon"><svg width="18" height="18" viewBox="0 0 24 24"><path d="M6.6 10.8a15 15 0 0 0 6.6 6.6l2.2-2.2a1 1 0 0 1 1-.25 11 11 0 0 0 3.6.6 1 1 0 0 1 1 1V20a1 1 0 0 1-1 1A17 17 0 0 1 3 4a1 1 0 0 1 1-1h3.5a1 1 0 0 1 1 1 11 11 0 0 0 .6 3.6 1 1 0 0 1-.25 1z" fill="#f5821f"/></svg></span>
    <div><b>PHONE</b><span>+555 0199 3344</span></div>
  </div>
  <div class="abs contact-row" style="left:542px;top:254px">
    <span class="contact-icon"><svg width="20" height="14" viewBox="0 0 20 14"><rect x="0" y="0" width="20" height="14" rx="2" fill="#f5821f"/><polyline points="1,1 10,8 19,1" fill="none" stroke="#201a17" stroke-width="2"/></svg></span>
    <div><b>EMAIL</b><span>hello@goldensheaffeed.com</span></div>
  </div>

  <h3 class="abs footer-heading" style="left:958px;top:68px">Sitemap</h3>
  <ul class="abs sitemap" style="left:958px;top:113px">
    <li>Home</li><li>About</li><li>Feed</li><li>Bedding</li><li>Contact Us</li><li>Request Quote</li>
  </ul>

  <div class="abs footer-rule"></div>
  <p class="abs copyright">© Golden Sheaf bedding and feed 2021 | Privacy Policy | Terms of Use</p>
  <span class="abs social" style="left:917px;top:414px" role="img" aria-label="Social profile link"></span>
  <span class="abs social" style="left:968px;top:414px" role="img" aria-label="Social profile link"></span>
  <span class="abs social" style="left:1018px;top:414px" role="img" aria-label="Social profile link"></span>
</footer>

</body>
</html>
```